New Webpage for High Class Expert Witness Services Company

We are looking for a minimalist design for a webpage that just has our logo and an entry form offer to connect with one of our Liaisons.
The entry form should just ask for Name, Email, Contact Info and Description of Project.

Company Name is: The Marlowe Crest Advisory Services

Number of Pages Required

1 page

```html
<!DOCTYPE html>
<html lang="en">
<head>
<meta charset="utf-8">
<title>The Marlowe Crest Advisory Services — Contact</title>
<link href="https://fonts.googleapis.com/css2?family=Cinzel:wght@400&family=Poppins:wght@400;500&display=swap" rel="stylesheet">
<style>
  :root{
    --page-bg:#f7f7f7;
    --card-bg:#ffffff;
    --panel-bg:#ebebeb;
    --ink:#151515;
    --text:#3a3a3a;
    --muted:#8a8a8a;
    --line:#cfcfcf;
    --footer-bg:#111111;
    --hero-dark:#2b2e31;
    --hero-light:#5d6266;
    --silver:#d9d9d9;
  }
  *{box-sizing:border-box;margin:0;padding:0}
  html,body{width:1200px;height:1125px;overflow:hidden}
  body{background:var(--page-bg);font-family:"Poppins",sans-serif;color:var(--text);position:relative}

  .hero{position:absolute;left:0;top:0;width:1200px;height:388px;
    background:radial-gradient(ellipse at 75% 30%,var(--hero-light) 0%,var(--hero-dark) 65%,#1f2225 100%)}
  .brand-name{position:absolute;left:0;top:132px;width:1200px;text-align:center;
    font-family:"Poppins",sans-serif;font-weight:500;font-size:26px;letter-spacing:2px;line-height:36px;
    color:var(--silver);text-transform:uppercase}

  .card{position:absolute;left:141px;top:315px;width:918px;height:661px;background:var(--card-bg);
    border-radius:14px;box-shadow:0 12px 40px rgba(0,0,0,.08)}

  .intro{position:absolute;left:57px;top:80px;width:330px}
  .intro h1{font-family:"Cinzel",serif;font-weight:400;font-size:36px;color:var(--ink);line-height:1.1}
  .intro p{font-size:13px;line-height:19px;margin-top:10px}

  .feature{position:absolute;left:57px;width:340px;display:flex;gap:17px}
  .feature-icon{flex:none;width:49px;height:49px;border-radius:50%;
    background:linear-gradient(145deg,#e4e4e4,#9d9d9f);display:flex;align-items:center;justify-content:center}
  .feature h3{font-size:14.5px;font-weight:500;color:var(--ink);margin-top:2px}
  .feature p{font-size:13px;line-height:19px;margin-top:7px}

  .divider{position:absolute;left:57px;top:487px;width:319px;height:1px;background:var(--line)}
  .social-title{position:absolute;left:57px;top:516px;font-size:15px;font-weight:500;color:var(--ink)}
  .social{position:absolute;left:57px;top:553px;display:flex;align-items:center;gap:16px}
  .social-dot{width:22px;height:22px;border-radius:50%;border:2px solid #555}
  .social-dot.active{width:33px;height:33px;background:var(--ink);border:none}

  .form-panel{position:absolute;left:440px;top:60px;width:421px;height:541px;background:var(--panel-bg);border-radius:14px}
  .form-panel h2{position:absolute;left:34px;top:31px;font-family:"Cinzel",serif;font-weight:400;font-size:30px;color:var(--ink)}
  .field-label{position:absolute;left:36px;font-size:13px;line-height:18px;color:var(--text)}
  .field{position:absolute;left:34px;width:353px;height:42px;background:#fff;border-radius:6px;
    display:flex;align-items:center;justify-content:space-between;padding:0 16px;font-size:13px;color:var(--muted)}
  .field.area{height:85px;align-items:flex-start;padding-top:12px}
  .submit{position:absolute;left:34px;top:462px;width:353px;height:45px;background:var(--ink);border-radius:6px;
    color:#fff;font-size:13px;font-weight:500;display:flex;align-items:center;justify-content:center;gap:10px}

  .footer{position:absolute;left:0;top:1055px;width:1200px;height:70px;background:var(--footer-bg);
    color:#e9e9e9;font-size:13px;display:flex;align-items:center;justify-content:center}
</style>
</head>
<body>
  <div class="hero" role="img" aria-label="Photo of medical experts working together in a clinic, darkened"></div>
  <div class="brand-name">The Marlowe Crest Advisory Services</div>

  <main class="card">
    <section class="intro">
      <h1>GET IN TOUCH</h1>
      <p>Lorem ipsum dolor amet, consectetuer adipiscing elit. Aenean commodo ligula eget dolor.</p>
    </section>

    <div class="feature" style="top:194px">
      <div class="feature-icon"><svg width="22" height="24" viewBox="0 0 22 24"><path d="M11 1 20 4.5v7c0 5.5-4 9.5-9 11.5C6 21 2 17 2 11.5v-7z" fill="#fff"/><path d="M7 12l3 3 5-6" fill="none" stroke="#999" stroke-width="2"/></svg></div>
      <div><h3>NATO-grade confidentiality</h3><p>Aenean massa. Cum sociis natoque penatibus et magnis parturient montes.</p></div>
    </div>
    <div class="feature" style="top:294px">
      <div class="feature-icon"><svg width="24" height="24" viewBox="0 0 24 24"><circle cx="12" cy="12" r="10" fill="#fff"/><path d="M7.5 12l3 3 6-6" fill="none" stroke="#999" stroke-width="2"/></svg></div>
      <div><h3>30+ expert witnesses</h3><p>Aenean massa. Cum sociis natoque penatibus et magnis parturient montes.</p></div>
    </div>
    <div class="feature" style="top:394px">
      <div class="feature-icon"><svg width="26" height="26" viewBox="0 0 26 26" fill="none" stroke="#fff" stroke-width="1.8"><circle cx="13" cy="13" r="11"/><ellipse cx="13" cy="13" rx="5" ry="11"/><path d="M2 13h22M4 7h18M4 19h18"/></svg></div>
      <div><h3>Global defense network</h3><p>Aenean massa. Cum sociis natoque penatibus et magnis parturient montes.</p></div>
    </div>

    <div class="divider"></div>
    <div class="social-title">Follow our social media</div>
    <div class="social">
      <span class="social-dot active" role="img" aria-label="Social network link"></span>
      <span class="social-dot" role="img" aria-label="Video channel link"></span>
      <span class="social-dot" role="img" aria-label="Professional network link"></span>
      <span class="social-dot" role="img" aria-label="Photo network link"></span>
    </div>

    <form class="form-panel">
      <h2>SEND US MESSAGE</h2>
      <div class="field-label" style="top:80px">Your Name</div>
      <div class="field" style="top:104px">Enter your name
        <svg width="18" height="18" viewBox="0 0 18 18" fill="none" stroke="#222" stroke-width="1.4"><circle cx="9" cy="5.5" r="3.8"/><path d="M2 17c0-4 3-6.5 7-6.5s7 2.5 7 6.5"/></svg></div>
      <div class="field-label" style="top:162px">Your Email</div>
      <div class="field" style="top:186px">Enter your Email
        <svg width="19" height="14" viewBox="0 0 19 14" fill="none" stroke="#222" stroke-width="1.3"><rect x="1" y="1" width="17" height="12"/><path d="M1 1l8.5 7L18 1M1 13l6-5.5M18 13l-6-5.5"/></svg></div>
      <div class="field-label" style="top:244px">Your Contact</div>
      <div class="field" style="top:268px">Enter your Contact
        <svg width="18" height="18" viewBox="0 0 18 18" fill="none" stroke="#222" stroke-width="1.3"><path d="M4 1.5l3 3.5-1.8 2c1 2 3 4 5 5l2-1.8 3.5 3-1.8 2.3C8 16 2 10 1.5 4z"/><path d="M11 1.5a6 6 0 0 1 5.5 5.5M11 4.5a3 3 0 0 1 2.5 2.5"/></svg></div>
      <div class="field-label" style="top:326px">Description of Project</div>
      <div class="field area" style="top:350px">Enter here...
        <svg width="19" height="19" viewBox="0 0 19 19" fill="none" stroke="#222" stroke-width="1.3"><path d="M9.5 1a8.5 8.5 0 1 1-4 16L1 18l1.2-4A8.5 8.5 0 0 1 9.5 1z"/><circle cx="6" cy="9.5" r=".8" fill="#222"/><circle cx="9.5" cy="9.5" r=".8" fill="#222"/><circle cx="13" cy="9.5" r=".8" fill="#222"/></svg></div>
      <div class="submit">CONNECT WITH A LIAISON
        <svg width="22" height="12" viewBox="0 0 22 12" fill="none" stroke="#fff" stroke-width="2"><path d="M0 6h20M15 1l5 5-5 5"/></svg></div>
    </form>
  </main>

  <footer class="footer">© 2026 the marlowe crest advisory services all right</footer>
</body>
</html>
```